Business Card Design

We are a manufacturing and distribution company with most of our customer base being supermarkets. We have established brand guidelines that are attached.

```html
<!DOCTYPE html>
<html lang="en">
<head>
<meta charset="utf-8">
<title>Corvella Business Card</title>
<link rel="stylesheet" href="https://fonts.googleapis.com/css2?family=Montserrat:wght@700;800&family=Arimo:wght@400;700&display=swap">
<style>
  :root {
    --backdrop: #c9c9c9;
    --card-white: #ffffff;
    --brand-blue: #0a68b0;
    --brand-red: #e0242c;
    --ink: #161616;
    --ink-soft: #333333;
  }
  * { box-sizing: border-box; margin: 0; padding: 0; }
  html, body { width: 1200px; height: 788px; overflow: hidden; }
  body {
    background: var(--backdrop);
    font-family: "Arimo", Arial, sans-serif;
    position: relative;
  }
  .card {
    position: absolute;
    border-radius: 22px;
    overflow: hidden;
    box-shadow: 0 10px 30px rgba(0,0,0,0.25);
  }

  /* Front card (portrait) */
  .card-front {
    left: 150px; top: 104px;
    width: 340px; height: 580px;
    background: var(--card-white);
  }
  .front-brand {
    position: absolute; top: 110px; left: 0; right: 0;
    display: flex; align-items: center; justify-content: center; gap: 12px;
  }
  .brand-name {
    font-family: "Montserrat", Arial, sans-serif;
    font-weight: 800;
    font-size: 40px;
    letter-spacing: 1px;
    color: var(--ink);
  }
  .brand-square {
    width: 30px; height: 30px; background: var(--brand-red);
  }
  .person {
    position: absolute; top: 220px; left: 0; right: 0; text-align: center;
  }
  .person-name {
    font-family: "Montserrat", Arial, sans-serif;
    font-weight: 700; font-size: 26px; letter-spacing: 0.5px;
  }
  .person-name .first { color: var(--brand-red); }
  .person-name .last { color: var(--brand-blue); }
  .person-role { font-size: 14px; color: var(--ink-soft); margin-top: 4px; }

  .front-band {
    position: absolute; left: 0; right: 0; top: 340px; bottom: 0;
    background: var(--brand-blue);
    border-top: 3px solid var(--brand-red);
  }
  .contact-icons {
    position: absolute; top: 322px; left: 50%; transform: translateX(-50%);
    display: flex; gap: 8px;
  }
  .icon {
    width: 34px; height: 34px; border-radius: 50%;
    background: var(--brand-red); border: 3px solid var(--card-white);
    display: flex; align-items: center; justify-content: center;
  }
  .icon svg { width: 16px; height: 16px; }
  .contact-list {
    position: absolute; top: 385px; left: 0; right: 0;
    text-align: center; color: var(--card-white);
    font-size: 15px; line-height: 23px;
  }
  .contact-rule {
    width: 140px; height: 1px; background: var(--brand-red);
    margin: 8px auto;
  }

  /* Back card (landscape) */
  .card-back {
    left: 560px; top: 224px;
    width: 580px; height: 360px;
    background: var(--brand-blue);
  }
  .back-brand {
    position: absolute; left: 50%; top: 50%;
    transform: translate(-50%, -50%) rotate(90deg);
    display: flex; align-items: center; gap: 16px;
  }
  .back-brand .brand-name { color: var(--card-white); font-size: 52px; }
</style>
</head>
<body>

  <section class="card card-front" aria-label="Business card front">
    <div class="front-brand">
      <span class="brand-name">CORVELLA</span>
      <span class="brand-square"></span>
    </div>
    <div class="person">
      <p class="person-name"><span class="first">DANA</span> <span class="last">WHITLOW</span></p>
      <p class="person-role">CEO/Founder</p>
    </div>

    <div class="front-band"></div>

    <div class="contact-icons">
      <span class="icon" aria-label="Phone">
        <svg viewBox="0 0 16 16"><path d="M4 1l3 3-1.5 1.5a8 8 0 0 0 5 5L12 9l3 3-2 2C7 14 2 9 2 3z" fill="#fff"/></svg>
      </span>
      <span class="icon" aria-label="Fax">
        <svg viewBox="0 0 16 16"><rect x="4" y="1" width="8" height="4" fill="#fff"/><rect x="1" y="6" width="14" height="6" rx="1" fill="#fff"/><rect x="4" y="10" width="8" height="5" fill="#fff" stroke="#e0242c"/></svg>
      </span>
      <span class="icon" aria-label="Email">
        <svg viewBox="0 0 16 16"><rect x="1" y="3" width="14" height="10" fill="#fff"/><path d="M1 3l7 6 7-6" fill="none" stroke="#e0242c" stroke-width="1.5"/></svg>
      </span>
      <span class="icon" aria-label="Website">
        <svg viewBox="0 0 16 16"><circle cx="8" cy="8" r="6.5" fill="none" stroke="#fff" stroke-width="1.5"/><ellipse cx="8" cy="8" rx="3" ry="6.5" fill="none" stroke="#fff"/><path d="M1.5 8h13" stroke="#fff"/></svg>
      </span>
    </div>

    <div class="contact-list">
      <p>(555) 201 3390</p>
      <p>(555) 201 3391</p>
      <p>hello@corvella.com.au</p>
      <p>www.corvella.com.au</p>
      <div class="contact-rule"></div>
      <p>1420 Kestrel Lane</p>
      <p>Country Name, AB 20145</p>
    </div>
  </section>

  <section class="card card-back" aria-label="Business card back">
    <div class="back-brand">
      <span class="brand-name">CORVELLA</span>
      <span class="brand-square"></span>
    </div>
  </section>

</body>
</html>
```